Elevate our existing website to be more luxury and add your pizazz!

We are seeking someone to bring some freshness to our recently redesigned website. I feel like it is missing some of the luxury, high end and rustic feelings we wanted from it. It is missing some pizazz! My goal was to have an intuitive, immersive, and captivating high-end website that resonates with my handmade art. I wanted a blend of creativity, rustic charm, luxury and high-end functionality, ensuring an easy-to-use and secure browsing experience that speaks to our brand of hand made and crafted items.
Design Aesthetics:
I love immersive nature. I'd love to feel like my website was a walk in the forest, the flowers, etc. Leaving the visitor feeling refreshed and inspired.
The design should seamlessly merge rustic elements with modern inspiration, evoking a sense of being surrounded by nature.
We're drawn to a moody ambiance that captures the essence of a forest, without veering into darkness.
While avoiding the typical all-white background, we aim for a balanced and visually appealing color scheme with perhaps elements floating into the frame with artful taste.
The site was designed in Elementor and I can provide you with the Wordpress login to make the changes once approved.
Branding Guide: https://www.plinthbox.com/design/QRmZtPeLqWs/VnTy82KdRoEuJxCbMa4wGp/watch?utm_content=QRmZtPeLqWs&utm_campaign=designshare&utm_medium=link&utm_source=publishsharelink
Recently redesigned website: dev.mossrivertwine.com
Target Market(s)
Luxury Crafters , Knitters and Crocheters
Industry/Entity Type
Art
Number of Pages Required
1 page

```html
<!DOCTYPE html>
<html lang="en">
<head>
<meta charset="utf-8">
<title>Moss River Twine — Handmade Hooks</title>
<link rel="stylesheet" href="https://fonts.googleapis.com/css2?family=Gilda+Display&family=Poppins:wght@400;500&display=swap">
<style>
:root{
  --forest:#34473a;
  --forest-deep:#2c3d31;
  --forest-mist:#5f7466;
  --paper:#e4e4e2;
  --paper-light:#ececea;
  --ink:#2b2b2b;
  --ink-soft:#3d3d3d;
  --white:#ffffff;
  --gold:#d9a300;
  --dot:#bfc2bf;
}
*{box-sizing:border-box;margin:0;padding:0}
html,body{width:1200px;height:4655px;overflow:hidden}
body{position:relative;background:var(--paper);font-family:"Poppins",sans-serif;color:var(--ink)}
.abs{position:absolute}
.btn{position:absolute;display:flex;align-items:center;justify-content:center;font-family:"Gilda Display",serif;font-size:16px}
.btn-dark{background:var(--forest);color:var(--white)}
.btn-light{background:var(--paper-light);color:var(--ink)}
.photo{position:absolute}

/* header */
.site-header{position:absolute;left:0;top:0;width:1200px;height:103px;background:var(--paper)}
.brand{position:absolute;display:flex;align-items:center;gap:12px;font-family:"Gilda Display",serif;color:var(--ink)}
.brand-mark{width:30px;height:30px;border-radius:50%;background:var(--ink)}
.brand-name{font-size:24px;line-height:1}
.brand-sub{font-size:11px;display:block;margin-top:4px}
.main-nav{position:absolute;top:38px;font-family:"Gilda Display",serif;font-size:15px;color:var(--ink)}
.main-nav span{position:absolute;white-space:nowrap}
.header-icons svg{position:absolute;top:40px}

/* hero */
.hero-bg{position:absolute;left:0;top:103px;width:1200px;height:617px;background:linear-gradient(180deg,#3d5143 0%,#4f6656 40%,#3a4e40 75%,#2f4235 100%)}
.hero-title{position:absolute;left:108px;top:252px;font-family:"Gilda Display",serif;font-weight:400;font-size:46px;color:var(--white);white-space:nowrap}
.hero-text{position:absolute;left:108px;top:328px;width:410px;font-size:16px;line-height:26px;color:var(--white)}
.hero-wave{position:absolute;left:0;top:590px}

/* text blocks */
.section-title{position:absolute;font-family:"Gilda Display",serif;font-weight:400;color:var(--ink)}
.body-text{position:absolute;font-size:16px;line-height:26.6px;color:var(--ink-soft);text-align:justify}

/* forest band */
.forest-band{position:absolute;left:0;width:1200px}
.craft-card{position:absolute;width:293px;height:385px;background:var(--paper-light)}
.craft-card .photo{left:0;top:0;width:293px;height:331px}
.craft-card .label{position:absolute;left:0;top:331px;width:293px;height:54px;display:flex;align-items:center;justify-content:center;font-family:"Gilda Display",serif;font-size:21px;color:var(--ink)}

/* products */
.product{position:absolute;width:330px}
.product .photo{position:relative;width:295px;height:289px;border-radius:6px}
.product-name{font-family:"Gilda Display",serif;font-size:22px;margin-top:28px;white-space:nowrap}
.product-price{font-size:17px;font-weight:500;margin-top:6px}
.stars{color:var(--gold);font-size:16px;letter-spacing:1px;margin-top:4px}
.slider-arrow{position:absolute;top:2876px;width:44px;height:44px;border:2px solid var(--ink);border-radius:50%;display:flex;align-items:center;justify-content:center}

/* press */
.press-badge{position:absolute;background:#d3d3d0;border-radius:8px}

/* instagram */
.insta-tile{position:absolute;top:3975px;width:221px;height:237px}
.pager-dot{position:absolute;top:4254px;width:18px;height:18px;border-radius:50%;background:var(--dot)}
.pager-dot.active{background:var(--forest)}

/* footer */
.footer-nav{position:absolute;top:4512px;font-family:"Gilda Display",serif;font-size:16px;color:var(--white)}
.footer-nav span{position:absolute;white-space:nowrap}
.copyright{position:absolute;right:112px;top:4548px;font-size:14px;color:#cdd3cd;white-space:nowrap}
.social{position:absolute;top:4555px;width:44px;height:44px;border-radius:50%;background:#4a5c4e}
</style>
</head>
<body>

<header class="site-header">
  <div class="brand" style="left:112px;top:26px">
    <span class="brand-mark"></span>
    <span><span class="brand-name">Moss River Twine</span><span class="brand-sub">by fenn studio</span></span>
  </div>
  <nav class="main-nav">
    <span style="left:450px">Home</span>
    <span style="left:526px">About Us</span>
    <span style="left:623px">Shop</span>
    <span style="left:692px">Custom Order</span>
    <span style="left:826px">Feedback</span>
    <span style="left:927px">Contact</span>
  </nav>
  <div class="header-icons">
    <svg style="left:1006px" width="18" height="18" viewBox="0 0 18 18" fill="none" stroke="#2b2b2b" stroke-width="2"><circle cx="7.5" cy="7.5" r="5.5"/><path d="M12 12l5 5"/></svg>
    <svg style="left:1037px" width="18" height="18" viewBox="0 0 18 18" fill="none" stroke="#2b2b2b" stroke-width="1.8"><circle cx="9" cy="5.5" r="3.8"/><path d="M2 17c0-4 3-6 7-6s7 2 7 6"/></svg>
    <svg style="left:1070px" width="20" height="18" viewBox="0 0 20 18" fill="#2b2b2b"><path d="M0 1h3.5l2.5 10h11l2-7H5" fill="none" stroke="#2b2b2b" stroke-width="1.8"/><path d="M5 4h15l-2 7H6z"/><circle cx="7.5" cy="15.5" r="1.8"/><circle cx="16" cy="15.5" r="1.8"/></svg>
  </div>
</header>

<section class="hero">
  <div class="hero-bg" role="img" aria-label="Misty pine forest in deep green tones"></div>
  <svg class="hero-wave" width="1200" height="130" viewBox="0 0 1200 130">
    <path d="M0 20 Q600 150 1200 20 L1200 130 L0 130 Z" fill="var(--paper)"/>
    <path d="M60 90 Q600 150 1200 20 Q620 175 60 90 Z" fill="var(--forest-deep)"/>
    <path d="M60 90 Q600 145 1200 20" fill="none" stroke="var(--white)" stroke-width="2"/>
  </svg>
  <h1 class="hero-title">From Nature, Refined</h1>
  <p class="hero-text">Inspired by the beauty and usefulness of wood, I started playing with sticks. This is my process of realizing their potential.</p>
  <a class="btn btn-light" style="left:108px;top:441px;width:194px;height:43px">Shop Now</a>
  <div class="abs" style="left:696px;top:217px;width:356px;height:361px;background:var(--paper-light);border-radius:10px"></div>
  <div class="photo" style="left:721px;top:172px;width:365px;height:383px;border-radius:10px;background:linear-gradient(150deg,#6b6552,#4c4a3f 45%,#8c7a5e 70%,#5a5446)" role="img" aria-label="Hand holding carved wooden crochet hooks above bark, carving knives and wood shavings"></div>
</section>

<section class="craft-intro">
  <div class="photo" style="left:231px;top:802px;width:351px;height:369px;border-radius:30px 175px 30px 30px;background:linear-gradient(160deg,#556b4e,#3e4a36 40%,#a0764e 70%,#6d4b30)" role="img" aria-label="Stacked cut logs in a pine forest"></div>
  <div class="photo" style="left:112px;top:882px;width:181px;height:247px;border-radius:90px 90px 8px 8px;background:linear-gradient(180deg,#d8cfb9 0%,#6c6e70 35%,#4c4f50 70%,#3e4a38 100%);box-shadow:0 10px 20px rgba(0,0,0,.25)" role="img" aria-label="Carved hooks on slate with skeins of yarn and leaves"></div>
  <h2 class="section-title" style="left:642px;top:820px;width:430px;font-size:33px;line-height:53px">More Than Just Tools, It's Art For Your Craft.</h2>
  <p class="body-text" style="left:642px;top:938px;width:446px">I create heirloom crochet hooks and knitting needles: rustic, refined or embellished with hand-painted art. Each one is unique, and all are hand-carved from the trees that grace our landscape. Choose from live oak, aromatic camphor, cypress, pine and sometimes treats like avocado, basil, or found mystery wood.</p>
  <a class="btn btn-dark" style="left:643px;top:1111px;width:159px;height:44px">Shop Now</a>
</section>

<section class="forest-band" style="top:1258px;height:556px;background:linear-gradient(180deg,#3a4d3e,#4a6050 50%,#33463a)" role="img" aria-label="Dense evergreen forest backdrop">
  <div class="craft-card" style="left:114px;top:86px">
    <div class="photo" style="background:linear-gradient(150deg,#5f6466,#4a4e50 50%,#3c4434)" role="img" aria-label="Rustic carved hooks on slate with dried leaves"></div>
    <div class="label">Rustice Hooks</div>
  </div>
  <div class="craft-card" style="left:454px;top:86px">
    <div class="photo" style="background:linear-gradient(150deg,#a07a55,#d8cdb8 45%,#3f8a6a 60%,#e8e4da)" role="img" aria-label="Resin and wood hook resting on a log slice with yarn"></div>
    <div class="label">Rustice Hooks</div>
  </div>
  <div class="craft-card" style="left:795px;top:86px">
    <div class="photo" style="background:linear-gradient(150deg,#f2f1ef,#e6e3df 50%,#5a3c2a 60%,#ece9e5)" role="img" aria-label="Hand holding a box of carved wooden earrings"></div>
    <div class="label">Rustice Hooks</div>
  </div>
</section>

<section class="inspired">
  <h2 class="section-title" style="left:110px;top:1958px;font-size:36px">Inspired By Wood</h2>
  <p class="body-text" style="left:110px;top:2014px;width:439px">Wood is inspiring. Even fallen branches and sticks continue the life of the tree in their fibers and seem the perfect accompaniment to wool and other fiber work. My hooks are handmade using a variety of wood sources from our natural landscape.</p>
  <a class="btn btn-dark" style="left:112px;top:2163px;width:159px;height:43px">Learn More</a>
  <div class="photo" style="left:618px;top:1901px;width:349px;height:370px;border-radius:175px 30px 30px 30px;background:linear-gradient(160deg,#6e7a58,#4d5a3e 40%,#a5774c 70%,#5c3f2a)" role="img" aria-label="Cut log pile on a forest floor"></div>
  <div class="photo" style="left:904px;top:1984px;width:186px;height:248px;border-radius:93px 93px 8px 8px;background:linear-gradient(170deg,#7c8a85,#b99a6a 45%,#5f6e58 75%,#3e3a34);box-shadow:0 10px 20px rgba(0,0,0,.25)" role="img" aria-label="Hand-painted wooden hooks fanned over skeins of yarn"></div>
</section>

<section class="products">
  <h2 class="section-title" style="left:0;top:2348px;width:1200px;text-align:center;font-size:36px">Our Products</h2>
  <div class="product" style="left:112px;top:2434px">
    <div class="photo" style="background:linear-gradient(150deg,#f1f1ee,#dfe2dc 50%,#4a7f7a 70%,#f1f0ec)" role="img" aria-label="Glittering hooks beside a long plume"></div>
    <div class="product-name">Shimmer Plume Hook</div>
    <div class="product-price">$55.00</div>
    <div class="stars">★★★★☆</div>
  </div>
  <div class="product" style="left:448px;top:2434px">
    <div class="photo" style="background:linear-gradient(150deg,#f3f3f1,#ebe8e2 50%,#8c7ab0 75%,#f2f1ef)" role="img" aria-label="Carved hook next to a vase of purple flowers"></div>
    <div class="product-name">Meadow Sprig Hook</div>
    <div class="product-price">$150.00</div>
    <div class="stars">★★★★☆</div>
  </div>
  <div class="product" style="left:786px;top:2434px">
    <div class="photo" style="background:linear-gradient(180deg,#dfe8ee,#b8c9d4 45%,#8a6b58 60%,#e5ebee)" role="img" aria-label="Hand holding a painted hook against a snowy lake view"></div>
    <div class="product-name">Painted Blooms &amp; Ember Smoke</div>
    <div class="product-price">$165.00</div>
    <div class="stars">★★★★☆</div>
  </div>
  <div class="slider-arrow" style="left:536px"><svg width="14" height="20" viewBox="0 0 14 20"><path d="M11 2L3 10l8 8" fill="none" stroke="#2b2b2b" stroke-width="2"/></svg></div>
  <div class="slider-arrow" style="left:618px"><svg width="14" height="20" viewBox="0 0 14 20"><path d="M3 2l8 8-8 8" fill="none" stroke="#2b2b2b" stroke-width="2"/></svg></div>
</section>

<section class="forest-band" style="top:3009px;height:545px;background:linear-gradient(180deg,#3b4c3e,#53665a 50%,#324337)" role="img" aria-label="Shadowy forest of tall trunks">
</section>
<div class="photo" style="left:231px;top:3097px;width:353px;height:369px;border-radius:30px 176px 30px 30px;background:linear-gradient(100deg,#c2a368,#6a5a44 35%,#5a4634 60%,#7a8a4c 75%,#3b3128)" role="img" aria-label="Child hugging a tree trunk with a moss heart"></div>
<div class="photo" style="left:112px;top:3175px;width:183px;height:249px;border-radius:91px 91px 8px 8px;background:linear-gradient(180deg,#d6d2c0,#7d8a62 45%,#4b6a34 75%,#5c7a3a);box-shadow:0 10px 20px rgba(0,0,0,.25)" role="img" aria-label="Sun glowing through a live oak over grass"></div>
<h2 class="section-title" style="left:634px;top:3136px;font-size:38px;color:var(--white);white-space:nowrap">Explore the trees with me</h2>
<p class="body-text" style="left:634px;top:3203px;width:472px;color:var(--white)">Different trees are like personalities, they all have their unique qualities. I thought I would share some of them with you here, in the hopes of helping you decide which wood fits your needs best. But also, I love trees and I'm happy to introduce you to some of these lovely creatures that are apart of my craft and landscape.</p>
<a class="btn btn-light" style="left:636px;top:3374px;width:159px;height:43px">Shop Now</a>

<section class="press">
  <h2 class="section-title" style="left:0;top:3630px;width:1200px;text-align:center;font-size:36px">As Seen In</h2>
  <div class="press-badge" style="left:112px;top:3740px;width:190px;height:52px"></div>
  <div class="press-badge" style="left:416px;top:3722px;width:168px;height:90px"></div>
  <div class="press-badge" style="left:697px;top:3722px;width:107px;height:90px"></div>
  <div class="press-badge" style="left:922px;top:3740px;width:168px;height:52px"></div>
</section>

<section class="instagram">
  <h2 class="section-title" style="left:0;top:3894px;width:1200px;text-align:center;font-size:36px">Follow On Instagram</h2>
  <div class="insta-tile" style="left:110px;background:linear-gradient(150deg,#4a3a30,#8a6a52 50%,#d8d2cc)" role="img" aria-label="Carved wooden hair stick worn in dark hair"></div>
  <div class="insta-tile" style="left:363px;background:linear-gradient(160deg,#1e1c1a,#5a4230 45%,#a07a4a 60%,#1f1d1b)" role="img" aria-label="Sticks and dried orange slices on a dark surface"></div>
  <div class="insta-tile" style="left:614px;background:linear-gradient(140deg,#2c2a28,#8a8784 45%,#e6e2dc 60%,#55514d)" role="img" aria-label="Hand holding a hook beside feathers"></div>
  <div class="insta-tile" style="left:867px;background:linear-gradient(180deg,#5d8aa8,#a8c3d0 35%,#c4923e 60%,#5a3a36)" role="img" aria-label="Carved hooks standing in glass vases"></div>
  <span class="pager-dot" style="left:539px"></span>
  <span class="pager-dot" style="left:573px"></span>
  <span class="pager-dot active" style="left:607px"></span>
  <span class="pager-dot" style="left:642px"></span>
</section>

<footer>
  <svg class="abs" style="left:0;top:4340px" width="1200" height="315" viewBox="0 0 1200 315">
    <path d="M0 95 Q600 -40 1200 95 L1200 315 L0 315 Z" fill="var(--forest)"/>
    <path d="M0 100 Q600 -20 1140 30 Q600 20 0 100 Z" fill="var(--forest-deep)"/>
    <path d="M0 100 Q600 5 1140 30" fill="none" stroke="var(--white)" stroke-width="2"/>
  </svg>
  <div class="brand" style="left:112px;top:4488px;color:var(--white)">
    <span class="brand-mark" style="background:var(--white)"></span>
    <span><span class="brand-name">Moss River Twine</span><span class="brand-sub">by fenn studio</span></span>
  </div>
  <nav class="footer-nav">
    <span style="left:566px">Home</span>
    <span style="left:636px">About Us</span>
    <span style="left:732px">Shop</span>
    <span style="left:795px">Custom Order</span>
    <span style="left:931px">Feedback</span>
    <span style="left:1032px">Contact</span>
  </nav>
  <p class="copyright">Copyright © 2024 Moss River Twine – All rights reserved.</p>
  <span class="social" style="left:112px" aria-label="Social profile one"></span>
  <span class="social" style="left:180px" aria-label="Social profile two"></span>
  <span class="social" style="left:249px" aria-label="Social profile three"></span>
</footer>

</body>
</html>
```